Personal Blog

The wordpress blog style and layout should be similar to http://www.samfenwick.com

homepage: my photo, list of things, call to action then 3 boxes (The Blog, The Book and podcast)

Other pages: About us, Blog, Consulting, Contact

Target Market(s)

Web Marketing Consultant

Industry/Entity Type

Consulting

Colors
3277b5
33a6d7
f04a50
f68e4e
33b7a4

```html
<!DOCTYPE html>
<html lang="en">
<head>
<meta charset="utf-8">
<title>Karim Delano — Personal Blog</title>
<link href="https://fonts.googleapis.com/css2?family=Dosis:wght@400;500;600;700&family=Arimo:wght@400;700&display=swap" rel="stylesheet">
<style>
:root{
  --teal:#33b7a4;
  --teal-dark:#239a89;
  --ink:#222;
  --muted:#555;
  --header-bg:#1b302f;
  --footer-bg:#1e3433;
  --page:#f4f4f4;
  --line:#dcdcdc;
  --white:#fff;
}
*{box-sizing:border-box;margin:0;padding:0}
html,body{width:680px;height:1200px;overflow:hidden}
body{position:relative;background:var(--page);font-family:"Arimo",Arial,sans-serif;color:var(--ink)}
.abs{position:absolute}

/* header */
.site-header{position:absolute;left:0;top:0;width:680px;height:87px;background:linear-gradient(180deg,#223b3a,var(--header-bg))}
.brand{position:absolute;left:27px;top:20px;display:flex;align-items:center;gap:6px;font-family:"Dosis",sans-serif;font-weight:600;font-size:23px;color:var(--white)}
.brand-mark{width:14px;height:14px;background:var(--teal);border-radius:3px}
.main-nav{position:absolute;right:27px;top:31px;display:flex;gap:15px;font-family:"Dosis",sans-serif;font-weight:600;font-size:14px;color:var(--white)}
.main-nav .is-active{color:var(--teal)}

/* hero */
.hero{position:absolute;left:0;top:87px;width:680px;height:224px;background:var(--white);border-bottom:1px solid var(--line)}
.hero-title{position:absolute;left:31px;top:18px;font-family:"Dosis",sans-serif;font-weight:600;font-size:23px;line-height:29px;color:var(--ink);white-space:nowrap}
.hero-title em{font-style:normal;color:var(--teal)}
.topic-list{position:absolute;left:31px;top:87px;list-style:none;font-size:12.5px;line-height:23.3px}
.topic-list li::before{content:"›";color:var(--teal);font-weight:700;margin-right:10px}
.hero-photo{position:absolute;left:349px;top:70px;width:304px;height:154px;background:linear-gradient(90deg,#e6e8ea 0%,#cfd4d8 40%,#c7d0e0 70%,#f4f4f4 100%)}

/* testimonial */
.testimonial{position:absolute;left:0;top:312px;width:680px;height:92px;border-bottom:1px solid var(--line)}
.testimonial-text{position:absolute;left:62px;top:30px;width:560px;font-family:"Dosis",sans-serif;font-weight:500;font-size:14px;line-height:19px;color:#333}
.testimonial-cite{position:absolute;right:60px;top:68px;font-size:10px;color:var(--teal)}
.quote-mark{font-family:Georgia,serif;color:#c8c8c8;font-size:30px;line-height:1}

/* feature boxes */
.feature{position:absolute;top:417px;width:199px;height:217px;background:var(--white);border:2px solid var(--teal);text-align:center}
.feature-icon{position:absolute;left:50%;top:22px;width:84px;height:84px;margin-left:-42px;border-radius:50%;border:3px solid #e7e7e7;background:var(--white)}
.feature-icon svg{position:absolute;left:4px;top:4px}
.feature-title{position:absolute;left:0;right:0;top:112px;font-family:"Dosis",sans-serif;font-weight:700;font-size:18px;line-height:24px}
.feature-text{position:absolute;left:0;right:0;top:137px;font-size:9.5px;line-height:14px;color:#333;white-space:nowrap}
.pill{position:absolute;height:16px;padding:0 9px;border-radius:9px;font-size:9px;line-height:14px;font-weight:700;white-space:nowrap}
.pill-solid{background:var(--teal);color:var(--white);border:1px solid var(--teal)}
.pill-outline{background:var(--white);color:var(--teal);border:1px solid var(--teal)}
.feature .pill{left:50%;transform:translateX(-50%);bottom:-9px}

/* recent posts */
.section-label{position:absolute;left:0;width:680px;top:672px;text-align:center;font-family:"Dosis",sans-serif;font-weight:700;font-size:13px;color:#333}
.section-label::before,.section-label::after{content:"";position:absolute;top:8px;width:210px;border-top:1px solid var(--line)}
.section-label::before{left:70px}.section-label::after{right:70px}
.post{position:absolute;top:707px;width:144px;height:253px;background:var(--white);border:1px solid #cfcfcf}
.post-image{position:absolute;left:3px;top:3px;width:136px;height:106px}
.post-title{position:absolute;left:11px;right:4px;top:118px;font-family:"Dosis",sans-serif;font-weight:700;font-size:13px;line-height:16px;white-space:nowrap}
.post-title.is-hover{color:var(--teal)}
.post-text{position:absolute;left:11px;right:6px;top:172px;font-size:9px;line-height:12.5px;color:#333}
.post .pill{left:11px;top:218px}

/* footer */
.site-footer{position:absolute;left:0;top:997px;width:680px;height:203px;background:linear-gradient(180deg,#243d3c,var(--footer-bg));color:var(--white)}
.footer-heading{position:absolute;top:27px;font-family:"Dosis",sans-serif;font-weight:700;font-size:16px;letter-spacing:.3px}
.footer-copy{position:absolute;left:27px;top:54px;width:195px;font-size:9px;line-height:12.5px}
.footer-copy a{color:var(--teal);text-decoration:none}
.footer-copy .gap{display:block;height:6px}
.field{position:absolute;left:240px;width:191px;height:22px;background:var(--white);border-radius:3px;font-size:9px;color:#444;padding:6px 6px}
.join-button{position:absolute;left:240px;top:120px;width:191px;height:27px;background:var(--teal);border-radius:3px;text-align:center;font-family:"Dosis",sans-serif;font-weight:700;font-size:15px;line-height:27px}
.social{position:absolute;top:54px;width:32px;height:32px;background:#d8dcdc;border-radius:3px}
.social.is-hover{background:var(--teal)}
.footer-small{position:absolute;font-size:9px}
.footer-small a{color:var(--teal);text-decoration:none}
.copyright{position:absolute;left:0;width:680px;top:178px;text-align:center;font-size:9px}
.copyright a{color:var(--teal);text-decoration:none}
</style>
</head>
<body>

<header class="site-header">
  <div class="brand"><span class="brand-mark"></span>Karim Delano</div>
  <nav class="main-nav">
    <span class="is-active">ABOUT</span><span>BLOG</span><span>CONSULTING</span><span>RESOURCES</span><span>BOOK</span><span>CONTACT</span>
  </nav>
</header>

<section class="hero">
  <h1 class="hero-title">Test go here and <em>Product Management,</em> text here <em>Online Marketing,</em><br>to learn these topics:</h1>
  <ul class="topic-list">
    <li>Product Management</li>
    <li>Customer Development</li>
    <li>Digital Marketing</li>
    <li>Branding &amp; Reputation</li>
    <li>Entreprenership</li>
  </ul>
  <div class="hero-photo" role="img" aria-label="Portrait of the author in a shirt and red tie, seated at a desk beside a computer monitor"></div>
</section>

<section class="testimonial">
  <span class="quote-mark abs" style="left:327px;top:-8px">&#8221;</span>
  <span class="quote-mark abs" style="left:34px;top:28px;font-size:22px">&#8220;</span>
  <p class="testimonial-text">"... I was blown away by his breadth of industry knowledge, the straight talking delivery and collaborative format. A highly recommended social media expert and thought leader..."</p>
  <span class="quote-mark abs" style="left:612px;top:46px;font-size:22px">&#8221;</span>
  <p class="testimonial-cite">-Mara Linden - Marketing</p>
</section>

<article class="feature" style="left:27px">
  <div class="feature-icon"><svg width="70" height="70" viewBox="0 0 70 70"><circle cx="35" cy="35" r="35" fill="#33b7a4"/><path d="M20 24h22a4 4 0 0 1 4 4v10a4 4 0 0 1-4 4H30l-7 6v-6h-3a4 4 0 0 1-4-4V28a4 4 0 0 1 4-4z" fill="none" stroke="#fff" stroke-width="2.5"/><path d="M46 30h4a4 4 0 0 1 4 4v9a4 4 0 0 1-4 4h-2v5l-6-5h-6" fill="none" stroke="#fff" stroke-width="2.5"/></svg></div>
  <h2 class="feature-title">The Blog</h2>
  <p class="feature-text">Lorem Ipsum is simply dummy text of the<br>printing &amp; typesetting industry. Lorem Ipsum<br>has been industry's standard dummy text<br>ever since the 15000s.</p>
  <span class="pill pill-solid">Read More &#9432;</span>
</article>
<article class="feature" style="left:240px">
  <div class="feature-icon"><svg width="70" height="70" viewBox="0 0 70 70"><circle cx="35" cy="35" r="35" fill="#33b7a4"/><path d="M20 24h22a4 4 0 0 1 4 4v10a4 4 0 0 1-4 4H30l-7 6v-6h-3a4 4 0 0 1-4-4V28a4 4 0 0 1 4-4z" fill="none" stroke="#fff" stroke-width="2.5"/><path d="M46 30h4a4 4 0 0 1 4 4v9a4 4 0 0 1-4 4h-2v5l-6-5h-6" fill="none" stroke="#fff" stroke-width="2.5"/></svg></div>
  <h2 class="feature-title">The Book</h2>
  <p class="feature-text">Lorem Ipsum is simply dummy text of the<br>printing &amp; typesetting industry. Lorem Ipsum<br>has been industry's standard dummy text<br>ever since the 15000s.</p>
  <span class="pill pill-solid">Read More &#9432;</span>
</article>
<article class="feature" style="left:453px">
  <div class="feature-icon"><svg width="70" height="70" viewBox="0 0 70 70"><circle cx="35" cy="35" r="35" fill="#33b7a4"/><path d="M20 24h22a4 4 0 0 1 4 4v10a4 4 0 0 1-4 4H30l-7 6v-6h-3a4 4 0 0 1-4-4V28a4 4 0 0 1 4-4z" fill="none" stroke="#fff" stroke-width="2.5"/><path d="M46 30h4a4 4 0 0 1 4 4v9a4 4 0 0 1-4 4h-2v5l-6-5h-6" fill="none" stroke="#fff" stroke-width="2.5"/></svg></div>
  <h2 class="feature-title">Consulting</h2>
  <p class="feature-text">Lorem Ipsum is simply dummy text of the<br>printing &amp; typesetting industry. Lorem Ipsum<br>has been industry's standard dummy text<br>ever since the 15000s.</p>
  <span class="pill pill-solid">Read More &#9432;</span>
</article>

<h3 class="section-label">&#9656; RECENT POSTS &#9666;</h3>

<article class="post" style="left:27px">
  <div class="post-image" role="img" aria-label="Overhead view of a meeting table with laptops, coffee cups and papers" style="background:linear-gradient(135deg,#4a4038,#8a7a66 50%,#d8d4cc)"></div>
  <h4 class="post-title is-hover">Yet Another Video Post<br>Format With<br>Embedded Media <svg width="10" height="8" viewBox="0 0 10 8"><rect x="0" y="1" width="6" height="6" fill="currentColor"/><path d="M6 4l4-3v6z" fill="currentColor"/></svg></h4>
  <p class="post-text">Lorem Ipsum is simply dummy text of the printing &amp; typesetting industry.</p>
  <span class="pill pill-outline">Read More &#9432;</span>
</article>
<article class="post" style="left:187px">
  <div class="post-image" role="img" aria-label="Group of business people in suits applauding" style="background:linear-gradient(135deg,#e4e4e4,#6c6f78 50%,#2e3038)"></div>
  <h4 class="post-title">Yet Another Video Post<br>Format With<br>Embedded Media <svg width="10" height="8" viewBox="0 0 10 8"><rect x="0" y="1" width="6" height="6" fill="currentColor"/><path d="M6 4l4-3v6z" fill="currentColor"/></svg></h4>
  <p class="post-text">Lorem Ipsum is simply dummy text of the printing &amp; typesetting industry.</p>
  <span class="pill pill-outline">Read More &#9432;</span>
</article>
<article class="post" style="left:349px">
  <div class="post-image" role="img" aria-label="Hand touching floating digital interface panels" style="background:linear-gradient(135deg,#2a2c30,#5a5e66 55%,#8c9098)"></div>
  <h4 class="post-title">Yet Another Video Post<br>Format With<br>Embedded Media <svg width="10" height="8" viewBox="0 0 10 8"><rect x="0" y="1" width="6" height="6" fill="currentColor"/><path d="M6 4l4-3v6z" fill="currentColor"/></svg></h4>
  <p class="post-text">Lorem Ipsum is simply dummy text of the printing &amp; typesetting industry.</p>
  <span class="pill pill-outline">Read More &#9432;</span>
</article>
<article class="post" style="left:509px">
  <div class="post-image" role="img" aria-label="Hands typing on a keyboard next to a desk phone" style="background:linear-gradient(135deg,#f0f0f0,#b4b4b6 50%,#4a4a4e)"></div>
  <h4 class="post-title">Yet Another Video Post<br>Format With<br>Embedded Media <svg width="10" height="8" viewBox="0 0 10 8"><rect x="0" y="1" width="6" height="6" fill="currentColor"/><path d="M6 4l4-3v6z" fill="currentColor"/></svg></h4>
  <p class="post-text">Lorem Ipsum is simply dummy text of the printing &amp; typesetting industry.</p>
  <span class="pill pill-outline">Read More &#9432;</span>
</article>

<footer class="site-footer">
  <h5 class="footer-heading" style="left:27px">ENTREPRENEUR, SPEAKER,</h5>
  <p class="footer-copy">Lorem Ipsum is simply dummy text of the printing &amp; typesetting industry. Lorem Ipsum has been industry's standard dummy text ever since the 15000s.<span class="gap"></span>Lorem Ipsum is simply dummy text of the printing &amp; typesetting industry.<br><a href="#">[ Read the long-winded version! ]</a></p>

  <h5 class="footer-heading" style="left:240px">JOIN MY NEW BUSINESS</h5>
  <div class="field" style="top:56px">Enter your name...</div>
  <div class="field" style="top:87px">Enter your email...</div>
  <div class="join-button">JOIN FOR FREE!</div>

  <h5 class="footer-heading" style="left:453px">CONNECT WITH ME</h5>
  <span class="social is-hover" style="left:453px" aria-label="Social link 1"></span>
  <span class="social" style="left:493px" aria-label="Social link 2"></span>
  <span class="social" style="left:533px" aria-label="Social link 3"></span>
  <span class="social" style="left:575px" aria-label="Social link 4"></span>
  <span class="footer-small" style="left:525px;top:98px">OR</span>
  <span class="footer-small" style="left:489px;top:113px">Connect with via <a href="#">email</a></span>

  <p class="copyright">© 2014 K. Delano <a href="#">www.karimdelano.com</a> | All Right Reserved.</p>
</footer>

</body>
</html>
```